Business Card Design needed for start up company Halvora

In need of a new business card designed for a start up company based in Sydney, Halvora is a new start up innovative Company, our mission it to make property accessible for everyday Australian and to become the leading Real Estate platform in Australia. We want it to be fresh and clean.

Industry/Entity Type

Financial

Contact Information for Business Card

Section for Name
Section for Title

HALVORA - The Strength of Pooling
Mobile:
Direct:

Font styles to use
Sans Serif

Colors
33a6d7
0692cd
0255a3
ffffff

Requirements
Must have
• Logo, all business card details

```html
<!DOCTYPE html>
<html lang="en">
<head>
<meta charset="utf-8">
<title>Halvora business card</title>
<link rel="stylesheet" href="https://fonts.googleapis.com/css2?family=Open+Sans:wght@400;600;800&display=swap">
<style>
  :root {
    --navy: #1b4b86;
    --navy-deep: #0255a3;
    --sky: #33a6d7;
    --sky-strong: #0692cd;
    --paper: #ffffff;
    --ink-grey: #6d6f73;
    --backdrop: #3a3b3d;
  }
  * { box-sizing: border-box; margin: 0; padding: 0; }
  html, body {
    width: 1200px; height: 864px; overflow: hidden;
    background: var(--backdrop);
    font-family: "Open Sans", Arial, sans-serif;
  }
  .card {
    position: absolute; left: 300px;
    width: 600px; height: 343px;
    box-shadow: 0 10px 24px rgba(0,0,0,.45);
    overflow: hidden;
  }
  .card--front { top: 60px; background: var(--navy); }
  .card--back { top: 461px; background: var(--paper); }

  .brand { position: absolute; display: flex; align-items: center; gap: 10px; }
  .brand__dot { width: 58px; height: 58px; border-radius: 50%; background: var(--sky); flex: none; }
  .brand__name { font-weight: 800; font-size: 50px; letter-spacing: 1px; line-height: 1; }

  .card--front .brand { left: 0; right: 0; top: 118px; justify-content: center; }
  .card--front .brand__name { color: var(--paper); }
  .tagline {
    position: absolute; left: 0; right: 0; bottom: 52px;
    text-align: center; color: var(--paper); font-size: 13px; letter-spacing: .3px;
  }

  .card--back .brand { left: 36px; top: 140px; }
  .card--back .brand__dot { width: 50px; height: 50px; }
  .card--back .brand__name { color: var(--navy); font-size: 40px; }

  .divider { position: absolute; left: 322px; top: 58px; width: 1.5px; height: 190px; background: var(--navy); }

  .details { position: absolute; left: 344px; top: 56px; color: var(--ink-grey); font-size: 11.5px; line-height: 1.35; }
  .details__name { color: var(--navy); font-weight: 600; font-size: 19px; line-height: 1.1; }
  .details__title { font-size: 12px; margin-bottom: 14px; }
  .details__address { margin-bottom: 14px; }
  .contact { list-style: none; }
  .contact li { display: flex; align-items: center; gap: 6px; }
  .contact svg { width: 11px; height: 11px; flex: none; }

  .band {
    position: absolute; left: 0; right: 0; top: 262px; height: 40px;
    background: var(--navy);
    display: flex; align-items: center; justify-content: center;
    color: var(--paper); font-size: 13px; font-weight: 600; letter-spacing: .3px;
  }
</style>
</head>
<body>
  <section class="card card--front" aria-label="Card front">
    <div class="brand">
      <span class="brand__dot"></span>
      <span class="brand__name">HALVORA</span>
    </div>
    <p class="tagline">The Strength of Pooling</p>
  </section>

  <section class="card card--back" aria-label="Card back">
    <div class="brand">
      <span class="brand__dot"></span>
      <span class="brand__name">HALVORA</span>
    </div>
    <div class="divider"></div>
    <div class="details">
      <p class="details__name">Mara Ellison</p>
      <p class="details__title">President</p>
      <p class="details__address">48 Harbour Lane, Suite 210<br>NSW 2000, Australia</p>
      <ul class="contact">
        <li>
          <svg viewBox="0 0 12 12" aria-hidden="true"><path d="M2.5 1 L4.5 1 L5 3.5 L3.8 4.5 Q5 7 7.5 8.2 L8.5 7 L11 7.5 L11 9.5 Q10.5 11 9 11 Q1 10 1 3 Q1 1.5 2.5 1Z" fill="#0692cd"/></svg>
          02 8123 4567
        </li>
        <li>
          <svg viewBox="0 0 12 12" aria-hidden="true"><rect x="3" y="0.8" width="6" height="10.4" rx="1.2" fill="none" stroke="#0692cd" stroke-width="1.2"/><circle cx="6" cy="9.3" r=".7" fill="#0692cd"/></svg>
          04 1234 5678
        </li>
        <li>
          <svg viewBox="0 0 12 12" aria-hidden="true"><rect x="0.8" y="2.5" width="10.4" height="7" fill="#0692cd"/><path d="M0.8 2.5 L6 6.5 L11.2 2.5" fill="none" stroke="#fff" stroke-width="1"/></svg>
          hello@halvora.com.au
        </li>
      </ul>
    </div>
    <div class="band">www.halvora.com.au</div>
  </section>
</body>
</html>
```